Brimsett Gardening Fresh New Website

We are looking to create a simple fresh website for our landscaping business. The website should appeal to a 'high end' audience. We deal with a lot of Embassies and affluent clients who have extremely large gardens that are meticulously maintained. The site is about communicating our excellent landscaping and customer service skills and encouraging new clients to reach out and engage us to take care of their gardens.

The website is basically going to be our business card, it will have almost no functionality other than two 'contact us' forms, one for smaller clients and one for more detailed projects.

The website will not have a lot of written content and will have to show photos of beautifully landscaped gardens.

The main logo in black will influence the site, however, we are open to all suggestions.

We are expecting to have the following pages:
Home Page
Services
About Us
Contact Us
Showcase (photo gallery of our work)

We need someone who can code it to wordpress and be available for minor changes over a number of days. They will be simple tweaks.

```html
<!DOCTYPE html>
<html lang="en">
<head>
<meta charset="utf-8">
<title>Brimsett Gardening</title>
<link rel="stylesheet" href="https://fonts.googleapis.com/css2?family=Montserrat:wght@600;700;800&family=Poppins:wght@400;500;600&display=swap">
<style>
:root{
  --gold:#ad7b27;
  --gold-dark:#8f6418;
  --yellow:#f6d444;
  --ink:#1d1d1d;
  --dark:#231f20;
  --text:#555;
  --line:#e3e3e3;
  --white:#fff;
}
*{box-sizing:border-box;margin:0;padding:0}
html,body{width:1200px;height:3369px;overflow:hidden}
body{position:relative;background:var(--white);font-family:'Poppins',sans-serif;color:var(--ink)}
.abs{position:absolute}
.btn{position:absolute;display:flex;align-items:center;justify-content:center;background:var(--gold);color:var(--white);font-size:13px;font-weight:500;text-transform:uppercase;letter-spacing:.2px}
/* header */
.site-header{position:absolute;left:0;top:0;width:1200px;height:85px;background:var(--dark)}
.brand{position:absolute;color:var(--gold);font-family:'Poppins',sans-serif;font-weight:500;text-align:center;text-transform:uppercase}
.site-header .brand{left:141px;top:24px;width:90px;font-size:12px;letter-spacing:3px;line-height:17px}
.brand-mark{display:block;margin:0 auto 4px;border:1.5px solid var(--gold);border-radius:50%}
.nav a{position:absolute;top:33px;color:var(--white);font-size:13.5px;text-decoration:none}
.nav a.active{color:var(--yellow)}
/* hero */
.hero{position:absolute;left:0;top:85px;width:1200px;height:551px;background:linear-gradient(135deg,#4b5b3a 0%,#7b8465 35%,#5f6a52 55%,#34502a 100%)}
.hero-tag{position:absolute;left:141px;top:224px;height:51px;padding:0 16px;background:var(--white);display:flex;align-items:center;justify-content:center;white-space:nowrap;font-family:'Montserrat',sans-serif;font-weight:700;font-size:23px;color:#3b3b3b;text-transform:uppercase}
.hero-title{position:absolute;left:141px;top:288px;font-family:'Montserrat',sans-serif;font-weight:700;font-size:39px;line-height:52px;color:var(--white);text-transform:uppercase}
.quick{position:absolute;left:709px;top:107px;width:350px;height:504px;background:#f4f4f4}
.tabs{position:absolute;left:0;top:0;width:350px;height:37px}
.quick h3{position:absolute;top:52px;width:100%;text-align:center;font-size:16.5px;font-weight:500}
.field{position:absolute;left:19px;width:314px;height:42px;background:var(--white);border:1px solid var(--line);border-radius:3px;font-size:11.5px;color:#777;padding:12px 10px}
.field svg{position:absolute;right:10px;top:13px}
.check{position:absolute;font-size:10.5px;color:#333;display:flex;align-items:center;gap:7px}
.box{width:12px;height:12px;border:1px solid #ccc;background:var(--white);display:inline-block;position:relative}
.box.on{border-color:var(--gold)}
/* about */
.about-photo{position:absolute;left:118px;top:661px;width:510px;height:458px;background:radial-gradient(ellipse at 50% 50%,#6f9a4c 0%,#9fb987 45%,rgba(255,255,255,0) 75%)}
.eyebrow{position:absolute;font-family:'Montserrat',sans-serif;font-weight:700;color:var(--gold);text-transform:uppercase}
.section-title{position:absolute;font-family:'Montserrat',sans-serif;font-weight:700;color:var(--ink);text-transform:uppercase}
.about p{position:absolute;left:611px;width:448px;font-size:13px;line-height:22px;color:var(--text)}
.center-title{left:0;width:1200px;text-align:center;font-size:33px}
.rule{position:absolute;left:575px;width:50px;height:2px;background:var(--gold)}
/* services */
.services-band{position:absolute;left:0;top:1256px;width:1200px;height:746px;background:linear-gradient(180deg,#fff 0%,#dfe7e8 25%,#a8b29c 50%,#5f8a3c 80%,#6c8f45 100%)}
.tab{position:absolute;top:1208px;height:35px;display:flex;align-items:center;justify-content:center;font-size:12.5px;font-weight:500;text-transform:uppercase}
.photo{position:absolute;width:300px;height:241px}
.card-label{position:absolute;width:271px;height:54px;background:var(--white);display:flex;align-items:center;justify-content:center;gap:8px;font-size:15.5px;font-weight:600;box-shadow:0 2px 8px rgba(0,0,0,.08)}
.card-label.hot{background:var(--yellow);height:81px;width:272px;flex-direction:column;gap:2px}
/* testimonials */
.review{position:absolute;background:var(--white);border:1px solid #eee;box-shadow:0 2px 10px rgba(0,0,0,.05)}
.avatar{position:absolute;left:22px;width:59px;height:59px;border-radius:50%;background:linear-gradient(135deg,#3a4f6a,#8aa3b8)}
.review h4{position:absolute;left:91px;font-size:15.5px;font-weight:500}
.stars{position:absolute;left:91px;color:#f3c21b;font-size:13px;letter-spacing:2px}
.review p{position:absolute;left:22px;width:262px;font-size:13px;line-height:22px;color:var(--text)}
.arrow{position:absolute;top:2315px;width:42px;height:42px;border-radius:50%;background:var(--white);box-shadow:0 2px 10px rgba(0,0,0,.15);display:flex;align-items:center;justify-content:center}
/* gallery */
.tile{position:absolute;top:2601px;width:234px;height:247px}
/* footer */
.site-footer{position:absolute;left:0;top:2994px;width:1200px;height:375px;background:var(--dark);color:var(--white)}
.site-footer h5{position:absolute;top:62px;font-size:15.5px;font-weight:600;text-transform:uppercase}
.site-footer h5::after{content:"";position:absolute;left:0;top:28px;width:136px;height:1px;background:var(--gold)}
.flink{position:absolute;left:518px;font-size:13.5px;color:#eee}
.contact-item{position:absolute;left:848px;font-size:13px;line-height:19px}
.social{position:absolute;top:3244px;width:27px;height:27px;border:1.5px solid #ddd;border-radius:50%}
</style>
</head>
<body>

<header class="site-header">
  <div class="brand"><span class="brand-mark" style="width:14px;height:14px"></span>Brimsett<br><span style="font-size:8px;letter-spacing:3px">Gardening</span></div>
  <nav class="nav">
    <a class="active" href="#" style="left:433px">Home</a>
    <a href="#" style="left:513px">About Us</a>
    <a href="#" style="left:612px">Services</a>
    <a href="#" style="left:707px">Gallery</a>
    <a href="#" style="left:792px">Contact Us</a>
  </nav>
  <a class="btn" style="left:906px;top:25px;width:153px;height:34px">Request a Quote</a>
</header>

<section class="hero" role="img" aria-label="Aerial view of a landscaped garden with a stone statue, lawns and a red-roofed pavilion"></section>
<div class="hero-tag">Brimsett Gardening</div>
<h1 class="hero-title">Your Full<br>Landscaping &amp; Lawn<br>Care Experts</h1>
<a class="btn" style="left:141px;top:462px;width:155px;height:35px">Request a Quote</a>

<form class="quick">
  <svg class="tabs" viewBox="0 0 350 37"><path d="M20 0H190L174 37H40Z" fill="#f6d444"/><path d="M194 0H350V6L322 37H178Z" fill="#ad7b27"/></svg>
  <span class="abs" style="left:47px;top:11px;font-size:11.5px;font-weight:500">SMALLER CLIENTS</span>
  <span class="abs" style="left:198px;top:11px;font-size:11.5px;font-weight:500;color:#fff">LARGE CLIENTS</span>
  <h3>QUICK CONTACT</h3>
  <div class="field" style="top:83px">Name<svg width="14" height="14" viewBox="0 0 14 14" fill="none" stroke="#aaa"><circle cx="7" cy="4.5" r="3"/><path d="M1.5 13c0-3 2.5-5 5.5-5s5.5 2 5.5 5"/></svg></div>
  <div class="field" style="top:131px">Email<svg width="14" height="14" viewBox="0 0 14 14" fill="none" stroke="#aaa"><rect x="1.5" y="3" width="11" height="9"/><path d="M1.5 3l5.5 5 5.5-5"/></svg></div>
  <div class="field" style="top:178px">Phone<svg width="14" height="14" viewBox="0 0 14 14" fill="none" stroke="#aaa"><path d="M3 1.5l2 3-1.5 1.5a8 8 0 004.5 4.5L9.5 9l3 2-1.5 2C6 13 1 8 1.5 3z"/></svg></div>
  <div class="field" style="top:227px">Service Type<svg width="10" height="10" viewBox="0 0 10 10" fill="none" stroke="#888"><path d="M2 4l3 3 3-3"/></svg></div>
  <div class="field" style="top:275px;height:102px">Message</div>
  <label class="check" style="left:19px;top:384px"><span class="box"></span>Weekly Lawn Maintenance</label>
  <label class="check" style="left:193px;top:384px"><span class="box"></span>Spring Clean Up</label>
  <label class="check" style="left:19px;top:407px"><span class="box on"><svg width="10" height="10" viewBox="0 0 10 10" style="position:absolute;left:0;top:0"><path d="M1.5 5l2.5 2.5L8.5 2" fill="none" stroke="#ad7b27" stroke-width="1.6"/></svg></span>Fertilizer/weed Control</label>
  <label class="check" style="left:193px;top:407px"><span class="box"></span>Fall Clean Up</label>
  <label class="check" style="left:19px;top:430px"><span class="box"></span>Core Aeration</label>
  <span class="btn" style="left:19px;top:450px;width:314px;height:40px;font-size:14px">Submit</span>
</form>

<section class="about">
  <div class="about-photo" role="img" aria-label="Garden path with lavender and a lamp post seen through a soft leaf-shaped frame"></div>
  <div class="eyebrow" style="left:611px;top:752px;font-size:33px">About</div>
  <h2 class="section-title" style="left:611px;top:790px;font-size:33px">Brimsett Gardening</h2>
  <p style="top:861px">Duis aute irure dolor in reprehenderit in voluptate velit esse cillum dolore eu fugiat nulla pariatur.</p>
  <p style="top:911px">Lorem ipsum dolor sit amet, consectetur adipiscing elit, sed do eiusmod tempor incididunt ut labore et dolore magna aliqua. Ut enim ad minim veniam, quis nostrud exercitation ullamco laboris nisi ut aliquip ex ea commodo consequat.</p>
  <a class="btn" style="left:611px;top:1021px;width:153px;height:34px">Read More</a>
</section>

<div class="services-band" role="img" aria-label="Wide lawn with a paved path leading to a brick house"></div>
<h2 class="section-title center-title" style="top:1130px">Our Services</h2>
<div class="rule" style="top:1183px"></div>
<div class="tab" style="left:438px;width:159px;background:var(--yellow)">Landscape Service</div>
<div class="tab" style="left:603px;width:159px;background:var(--gold);color:#fff">Lawn Service</div>

<div class="photo" style="left:141px;top:1273px;background:linear-gradient(180deg,#8fc1e6,#cfe3f0 35%,#4f7a32 55%,#3d6d26)" role="img" aria-label="Manicured garden with trees in front of a large estate"></div>
<div class="photo" style="left:450px;top:1273px;background:linear-gradient(160deg,#c7c79a,#6f8e3f 45%,#b7b4ad 70%,#9d9a94)" role="img" aria-label="Sloped lawn next to a paved walkway"></div>
<div class="photo" style="left:759px;top:1273px;background:linear-gradient(135deg,#4a3a2e,#6b5444 50%,#3a2d24)" role="img" aria-label="Garden soil with terracotta pots and a trowel"></div>
<div class="card-label" style="left:156px;top:1484px"><svg width="38" height="38" viewBox="0 0 38 38" fill="none" stroke="#222" stroke-width="2"><rect x="3" y="3" width="22" height="32"/><path d="M3 14h9v21M16 3v11"/><path d="M28 6l6 6-10 10h-6v-6z" fill="#f6d444"/></svg>Design Service</div>
<div class="card-label hot" style="left:463px;top:1484px">
  <div style="display:flex;align-items:center;gap:10px"><svg width="66" height="40" viewBox="0 0 66 40" fill="none" stroke="#222" stroke-width="2"><path d="M2 8h12l8 18h34"/><path d="M24 12h32l-6 14" fill="#f6d444"/><circle cx="54" cy="32" r="6"/></svg><span>Mulch or Rock Install<br><span style="font-size:12.5px;font-weight:500;text-decoration:underline">Get A Estimate</span> →</span></div>
</div>
<div class="card-label" style="left:773px;top:1484px"><svg width="38" height="38" viewBox="0 0 38 38" fill="none" stroke="#222" stroke-width="2"><path d="M2 34h34"/><path d="M4 34l6-12 10 6 6 6" fill="#f6d444"/><path d="M20 24L32 6m-4-2l8 4"/></svg>Grading Rough</div>

<div class="photo" style="left:141px;top:1589px;background:linear-gradient(135deg,#d8577f,#5f8a3c 45%,#8b8b86 60%,#6a9a3e)" role="img" aria-label="Curved stone path beside a lawn and pink flowering shrubs"></div>
<div class="photo" style="left:450px;top:1589px;background:linear-gradient(180deg,#2c6ea8,#8c6b45 35%,#a37e52 60%,#4f8030)" role="img" aria-label="Rolls of fresh sod being laid on soil"></div>
<div class="photo" style="left:759px;top:1589px;background:linear-gradient(180deg,#e2e2de,#5a8c3a 55%,#2f4f23)" role="img" aria-label="Hedge and iron fence in front of a house"></div>
<div class="card-label" style="left:156px;top:1799px"><svg width="30" height="38" viewBox="0 0 30 38" fill="none" stroke="#222" stroke-width="2"><rect x="3" y="5" width="20" height="30"/><path d="M8 12h10M8 18h10M8 24h10M8 30h10"/><circle cx="24" cy="6" r="5" fill="#f6d444"/></svg>Grading</div>
<div class="card-label" style="left:463px;top:1799px"><svg width="40" height="38" viewBox="0 0 40 38" fill="none" stroke="#222" stroke-width="2"><rect x="2" y="6" width="8" height="28" rx="4"/><path d="M10 10h28v24H10"/><rect x="20" y="16" width="12" height="10" fill="#f6d444"/></svg>Sod Installation</div>
<div class="card-label" style="left:773px;top:1799px"><svg width="52" height="38" viewBox="0 0 52 38" fill="none" stroke="#222" stroke-width="2"><rect x="2" y="2" width="48" height="34"/><path d="M2 10h48M2 19h48M2 28h48M14 2v8M30 2v8M22 10v9M38 10v9M14 19v9M30 19v9M22 28v8M38 28v8"/><rect x="23" y="11" width="14" height="7" fill="#f6d444" stroke="none"/></svg>Retaining Walls</div>
<a class="btn" style="left:523px;top:1879px;width:154px;height:34px">Request a Quote</a>

<section>
  <h2 class="section-title center-title" style="top:2077px">What Our Clients Say</h2>
  <div class="rule" style="top:2129px"></div>
  <div class="arrow" style="left:76px"><svg width="14" height="14" viewBox="0 0 14 14"><path d="M9 2L4 7l5 5" fill="none" stroke="#111" stroke-width="2.2"/></svg></div>
  <div class="arrow" style="left:1083px"><svg width="14" height="14" viewBox="0 0 14 14"><path d="M5 2l5 5-5 5" fill="none" stroke="#111" stroke-width="2.2"/></svg></div>
  <article class="review" style="left:141px;top:2181px;width:300px;height:266px">
    <div class="avatar" style="top:22px" role="img" aria-label="Client portrait"></div>
    <h4 style="top:30px">Owen Hartley</h4><div class="stars" style="top:52px">★★★★★</div>
    <p style="top:96px">Lorem ipsum dolor sit amet, consectetur adipiscing elit, sed do eiusmod tempor incididunt ut labore et dolore magna aliqua. Ut enim ad minim veniam ut aut reiciendis voluptatibus maiores alias ut aut reiciendis voluptatibus.</p>
  </article>
  <article class="review" style="left:450px;top:2153px;width:300px;height:274px;border-bottom:5px solid var(--gold)">
    <div class="avatar" style="top:18px;background:linear-gradient(135deg,#2a2a2a,#9a8f86)" role="img" aria-label="Client portrait"></div>
    <h4 style="top:26px">Nadia Pryce</h4><div class="stars" style="top:48px">★★★★★</div>
    <p style="top:94px">Sed ut perspiciatis unde omnis iste natus error sit voluptatem accusantium doloremque laudantium, totam rem aperiam, eaque ipsa quae ab illo ipsum inventore veritatis et quasi architecto beatae vitae dicta sunt explicabo. Nemo enim ipsam voluptatem.</p>
  </article>
  <article class="review" style="left:759px;top:2181px;width:300px;height:266px">
    <div class="avatar" style="top:22px;background:linear-gradient(135deg,#1f3a2c,#6d7f70)" role="img" aria-label="Client portrait"></div>
    <h4 style="top:30px">Tomas R</h4><div class="stars" style="top:52px">★★★★★</div>
    <p style="top:96px">Lorem ipsum dolor sit amet, consectetur adipiscing elit, sed do eiusmod tempor incididunt ut labore et dolore magna aliqua. Ut enim ad minim veniam ut aut reiciendis voluptatibus maiores alias ut aut reiciendis voluptatibus.</p>
  </article>
</section>

<section>
  <h2 class="section-title center-title" style="top:2525px">Work Gallery</h2>
  <div class="rule" style="top:2577px"></div>
  <div class="tile" style="left:0;background:linear-gradient(180deg,#c9d9e4,#a79272 40%,#7fae2f 65%,#5d8d22)" role="img" aria-label="Houses behind a sunlit lawn"></div>
  <div class="tile" style="left:241px;background:linear-gradient(135deg,#c43b2c,#8d7b5e 30%,#6b5a45 60%,#e1c52b)" role="img" aria-label="Curved stone retaining wall with flower beds"></div>
  <div class="tile" style="left:483px;background:#f4d94f" role="img" aria-label="Garden project photo with caption overlay">
    <p style="position:absolute;left:22px;top:50px;width:190px;text-align:center;font-size:13px;line-height:22px;color:#333">Itaque earum rerum hic tenetur a sapiente delectus, ut aut reiciendis voluptatibus maiores alias consequatur aut perferendis doloribus asperiores repellat.</p>
  </div>
  <div class="tile" style="left:724px;background:linear-gradient(180deg,#a1384a,#3f6b2a 35%,#8e7d6a 70%,#5c7d37)" role="img" aria-label="Stone path through planted garden beds"></div>
  <div class="tile" style="left:966px;background:linear-gradient(180deg,#c9d9e4,#4d7b2d 40%,#6faa2e 75%,#88be3a)" role="img" aria-label="Open lawn bordered by trees"></div>
  <a class="btn" style="left:522px;top:2874px;width:154px;height:34px">View All</a>
</section>

<footer class="site-footer">
  <div class="brand" style="left:130px;top:68px;width:210px;font-size:27px;letter-spacing:9px;line-height:34px"><span class="brand-mark" style="width:40px;height:40px;margin-bottom:18px"></span>Brimsett<br><span style="font-size:15px;letter-spacing:7px">Gardening</span></div>
  <h5 style="left:518px">Quick Links</h5>
  <h5 style="left:848px">Contact Details</h5>
</footer>
<span class="social" style="left:169px"></span><span class="social" style="left:204px"></span><span class="social" style="left:239px"></span><span class="social" style="left:273px"></span>
<span class="flink" style="top:3096px">Home</span>
<span class="flink" style="top:3137px">Services</span>
<span class="flink" style="top:3178px">Gallery</span>
<span class="flink" style="top:3218px">About Us</span>
<span class="flink" style="top:3259px">contact Us</span>
<svg class="abs" style="left:850px;top:3098px" width="27" height="27" viewBox="0 0 27 27" fill="none" stroke="#fff" stroke-width="1.4"><circle cx="13.5" cy="13.5" r="12"/><path d="M1.5 13.5h24M13.5 1.5c-5 6-5 18 0 24M13.5 1.5c5 6 5 18 0 24"/></svg>
<div class="contact-item" style="left:884px;top:3098px;color:#fff">48 Larchmont Row, Suite 2<br>Fairbrook, ST 20417</div>
<svg class="abs" style="left:850px;top:3170px" width="30" height="28" viewBox="0 0 30 28" fill="none" stroke="#fff" stroke-width="1.4"><path d="M4 4l4 5-2 2a12 12 0 007 7l2-2 5 4-2 3C10 23 2 15 2 6z"/><circle cx="22" cy="8" r="6"/><path d="M19 8l2 2 4-4"/></svg>
<div class="contact-item" style="left:887px;top:3168px;color:#fff"><b style="font-weight:600">Phone</b><br>(555) 014-2298</div>
<svg class="abs" style="left:850px;top:3243px" width="27" height="30" viewBox="0 0 27 30" fill="none" stroke="#fff" stroke-width="1.4"><path d="M2 12l11.5-9L25 12v16H2z"/><path d="M2 12l11.5 9L25 12"/><path d="M6 9V5h15v4"/></svg>
<div class="contact-item" style="left:888px;top:3242px;color:#fff"><b style="font-weight:600">Email</b><br>hello@brimsettgardening.com</div>
<div class="abs" style="left:141px;top:3328px;width:918px;height:1px;background:#444"></div>
<div class="abs" style="left:0;top:3340px;width:1200px;text-align:center;font-size:13px;color:#ddd">© 2024 Brimsett Gardening. All Rights Reserved</div>

</body>
</html>
```